Design a compelling Tarnwove Business Card that will drive people to my site

I want a business card that I can give to people—less to tell them who I am and more to direct them to my website. My website is a portal for Pelmor Aquatics Officials and a place for people who want to become Pelmor Aquatics Officials.
I am uploading my official company logo as well as a business card mockup that I did on my own. Please feel free to completely stray from this design.
I've included a screen recording of the homepage of my website as well.
Target Market(s)
Pelmor Aquatics Officials and people who desire to become one
Contact Information for Business Card
website url
Look and feel
Each slider illustrates characteristics of the customer's brand and the style your logo design should communicate.

```html
<!DOCTYPE html>
<html lang="en">
<head>
<meta charset="utf-8">
<title>Tarnwove Business Card</title>
<link href="https://fonts.googleapis.com/css2?family=Montserrat:wght@400;500;600;700&display=swap" rel="stylesheet">
<style>
  :root {
    --brand-blue: #3a55a6;
    --brand-light: #8fa6da;
    --ink: #2b2f3a;
    --paper: #ffffff;
    --backdrop: #c9c9cb;
  }
  * { margin: 0; padding: 0; box-sizing: border-box; }
  html, body { width: 1200px; height: 802px; overflow: hidden; }
  body {
    background: var(--backdrop);
    font-family: "Montserrat", sans-serif;
    position: relative;
  }
  .card {
    position: absolute;
    top: 251px;
    width: 520px;
    height: 300px;
    border-radius: 18px;
    overflow: hidden;
  }
  .card-front { left: 60px; background: var(--paper); }
  .card-back { left: 620px; background: var(--brand-blue); }

  .front-swoosh { position: absolute; inset: 0; width: 520px; height: 300px; }

  .front-wordmark {
    position: absolute;
    left: 36px;
    top: 126px;
    font-size: 36px;
    font-weight: 600;
    color: var(--brand-blue);
    letter-spacing: -0.5px;
  }
  .front-divider {
    position: absolute;
    left: 238px;
    top: 62px;
    width: 1px;
    height: 140px;
    background: var(--brand-light);
  }
  .contact {
    position: absolute;
    left: 262px;
    top: 58px;
  }
  .contact-name { font-size: 20px; font-weight: 700; color: var(--brand-blue); }
  .contact-name .surname { color: var(--brand-light); }
  .contact-role { font-size: 12px; color: var(--ink); margin-top: 2px; }
  .contact-list { list-style: none; margin-top: 18px; }
  .contact-list li {
    display: flex;
    align-items: center;
    gap: 8px;
    font-size: 12px;
    color: var(--ink);
    line-height: 22px;
  }
  .contact-list svg { width: 12px; height: 12px; fill: var(--brand-blue); }

  .back-fill { position: absolute; inset: 0; background: var(--brand-blue); }
  .back-wordmark {
    position: absolute;
    inset: 0;
    display: flex;
    align-items: center;
    justify-content: center;
    font-size: 66px;
    font-weight: 600;
    color: var(--paper);
    letter-spacing: -1px;
  }
</style>
</head>
<body>
  <section class="card card-front">
    <svg class="front-swoosh" viewBox="0 0 520 300">
      <path d="M0,208 Q330,200 520,258" fill="none" stroke="var(--brand-light)" stroke-width="4"/>
      <path d="M0,218 Q330,212 520,270 L520,300 L0,300 Z" fill="var(--brand-blue)"/>
    </svg>
    <div class="front-wordmark">Tarnwove</div>
    <div class="front-divider"></div>
    <div class="contact">
      <div class="contact-name">Martin <span class="surname">Alvera</span></div>
      <div class="contact-role">CEO &amp; Founder</div>
      <ul class="contact-list">
        <li><svg viewBox="0 0 24 24"><path d="M6.6 10.8a15 15 0 0 0 6.6 6.6l2.2-2.2c.3-.3.7-.4 1-.2 1.1.4 2.3.6 3.6.6.6 0 1 .4 1 1V20c0 .6-.4 1-1 1C10.6 21 3 13.4 3 4c0-.6.4-1 1-1h3.5c.6 0 1 .4 1 1 0 1.3.2 2.5.6 3.6.1.3 0 .7-.2 1z"/></svg>(555) 014-2273</li>
        <li><svg viewBox="0 0 24 24"><path d="M2 5h20v14H2z M2 5l10 8 10-8" /></svg>martin@tarnwove.com</li>
        <li><svg viewBox="0 0 24 24"><circle cx="12" cy="12" r="10"/><path d="M2 12h20M12 2c3 3 3 17 0 20M12 2c-3 3-3 17 0 20" stroke="#fff" stroke-width="1.5" fill="none"/></svg>www.tarnwove.com</li>
      </ul>
    </div>
  </section>

  <section class="card card-back">
    <div class="back-fill" role="img" aria-label="Faint translucent bubble pattern on blue"></div>
    <div class="back-wordmark">Tarnwove</div>
  </section>
</body>
</html>
```